Heron Loan Partners Business Card

We need a business card design for our mortgage servicing company. In addition to servicing the loans of homeowners, we help homeowners with purchasing their homes and any mortgage refinancing. We would like to see designs that use the colors in the logo attached below (gold-ish yellow and navy blue), and any other design you deem fit! The design should communicate a simpler life with smart mortgages provided by Heron.

```html
<!DOCTYPE html>
<html lang="en">
<head>
<meta charset="utf-8">
<title>Heron Loan Partners Business Card</title>
<link rel="stylesheet" href="https://fonts.googleapis.com/css2?family=Montserrat:wght@600;700&family=Open+Sans:wght@400;600&display=swap">
<style>
  :root {
    --backdrop: #222222;
    --gold: #e1b03d;
    --gold-deep: #c9962a;
    --navy: #231d55;
    --ink: #1a1a1a;
    --paper: #ffffff;
  }
  * { box-sizing: border-box; margin: 0; padding: 0; }
  html, body { width: 1200px; height: 780px; overflow: hidden; }
  body { background: var(--backdrop); position: relative; font-family: "Open Sans", sans-serif; }

  .card {
    position: absolute;
    width: 580px;
    height: 331px;
    border-radius: 22px;
    overflow: hidden;
    box-shadow: 0 10px 28px rgba(0,0,0,.55);
  }

  /* Back of card */
  .card-back { left: 50px; top: 40px; background: var(--gold); }
  .card-back .pattern-area {
    position: absolute; inset: 0;
    background: linear-gradient(135deg, #d9a532 0%, var(--gold) 45%, #eac35e 100%);
  }
  .card-back .back-name {
    position: absolute; right: 70px; bottom: 120px;
    font-family: "Montserrat", sans-serif; font-weight: 700;
    font-size: 18px; color: var(--navy);
  }

  /* Front of card */
  .card-front { left: 570px; top: 410px; background: var(--paper); }
  .front-wave { position: absolute; inset: 0; }
  .brand-name {
    position: absolute; left: 40px; top: 128px; width: 190px;
    font-family: "Montserrat", sans-serif; font-weight: 700;
    font-size: 24px; line-height: 1.15; color: var(--gold);
    display: flex; align-items: center; gap: 10px;
  }
  .brand-dot { flex: none; width: 14px; height: 14px; border-radius: 50%; background: var(--navy); }
  .divider {
    position: absolute; left: 248px; top: 62px; width: 1px; height: 150px;
    background: var(--ink);
  }
  .details { position: absolute; left: 272px; top: 36px; }
  .person-name {
    font-family: "Montserrat", sans-serif; font-weight: 700;
    font-size: 25px; line-height: 1.1; white-space: nowrap;
  }
  .person-name .first { color: var(--gold); }
  .person-name .last { color: var(--navy); }
  .person-title {
    font-family: "Montserrat", sans-serif; font-weight: 600;
    font-size: 14px; color: var(--ink); margin-top: 4px;
  }
  .address { font-size: 12.5px; line-height: 1.4; color: var(--ink); margin-top: 10px; }
  .contacts { list-style: none; margin-top: 8px; font-size: 12.5px; color: var(--ink); }
  .contacts li { display: flex; align-items: center; gap: 8px; line-height: 1.5; }
  .contacts svg { width: 13px; height: 13px; flex: none; }
</style>
</head>
<body>

  <section class="card card-back" aria-label="Back of business card">
    <div class="pattern-area" role="img" aria-label="Repeating brand pattern in gold tones"></div>
    <span class="back-name">Heron</span>
  </section>

  <section class="card card-front" aria-label="Front of business card">
    <svg class="front-wave" viewBox="0 0 580 331" preserveAspectRatio="none" aria-hidden="true">
      <path d="M0 310 C 150 310, 270 296, 360 258 C 440 224, 510 208, 580 204 L580 331 L0 331 Z" fill="var(--gold)"/>
      <path d="M70 300 C 180 300, 270 270, 355 238 C 440 205, 510 192, 565 188 C 510 196, 440 214, 360 248 C 272 284, 180 298, 70 300 Z" fill="var(--navy)"/>
    </svg>

    <div class="brand-name"><span class="brand-dot"></span><span>Heron Loan Partners</span></div>
    <div class="divider"></div>

    <div class="details">
      <h1 class="person-name"><span class="first">Lenka</span> <span class="last">Dvorakova</span></h1>
      <p class="person-title">Managing Director</p>
      <p class="address">1840 Willow Bend Rd. Suite 310<br>Arlington, TX 76011</p>
      <ul class="contacts">
        <li>
          <svg viewBox="0 0 24 24"><path fill="var(--navy)" d="M6.6 10.8a15.1 15.1 0 0 0 6.6 6.6l2.2-2.2c.3-.3.7-.4 1-.2 1.1.4 2.300.6 3.6.6.6 0 1 .4 1 1V20c0 .6-.4 1-1 1C10.6 21 3 13.4 3 4c0-.6.4-1 1-1h3.5c.6 0 1 .4 1 1 0 1.3.2 2.5.6 3.6.1.3 0 .7-.2 1z"/></svg>
          (817) 555-0142
        </li>
        <li>
          <svg viewBox="0 0 24 24"><rect x="2" y="5" width="20" height="14" rx="2" fill="var(--navy)"/><path d="M3 6l9 7 9-7" stroke="#fff" stroke-width="1.6" fill="none"/></svg>
          hello@heronloans.com
        </li>
        <li>
          <svg viewBox="0 0 24 24"><circle cx="12" cy="12" r="10" fill="var(--navy)"/><path d="M2 12h20M12 2c3 3 3 17 0 20M12 2c-3 3-3 17 0 20" stroke="#fff" stroke-width="1.3" fill="none"/></svg>
          www.heronloans.com
        </li>
      </ul>
    </div>
  </section>

</body>
</html>
```